Velan Tea Label & packaging for a premium tea brand. For local and global market

Create a look and feel for a box and rectangle tin. We are looking for a luxe packaging design for a new tea brand based in Kenya called 'Velan Tea'. Kenya is home to the finest teas in the world and Velan tea looks to embody that fact. Velan Tea uses the most premium of Kenyan Tea, Black tea, Purple tea, White Tea, Green tea, Hibiscus Tea and Moringa Tea. Velan Tea is handpicked from Kenya's highlands. This project will include the look and feel of the different teas described above. The copy on the main face of the box should read 'Premium Kenyan Tea' The box will contain 25 tagged tea bags, with a net weight of 50 gms.

On one side of the box will read 'packaging instructions' To fully savour this Velan premium tea, use one tea bag for each cup, add some freshly bolded water and wait for 2 minutes as you enjoy the sweet aroma of our tea, stir and serve' Ingredients : Black Tea, and for the others the same : Hibiscus Tea, Green Tea, Purple Tea, White tea. should also feature on the label: Produce of Kenya.

Target Market(s)

Premium

Industry/Entity Type

Agribusiness

Font styles to use
Script

Colors

Designer to choose colors to be used in the design.

Requirements
Must have
• Luxe look and feel
Nice to have
• I have attached the Velan tea logo and images of brands I'd lile the designer to be inspired by.
Should not have
• Green and yellow colours

```html
<!DOCTYPE html>
<html lang="en">
<head>
<meta charset="utf-8">
<title>Velan Tea – Hibiscus Tea Tin Label</title>
<link rel="stylesheet" href="https://fonts.googleapis.com/css2?family=Josefin+Sans:wght@300&family=Libre+Baskerville:ital@0;1&family=Oswald:wght@300&display=swap">
<style>
  :root {
    --backdrop: #a7aaaf;
    --tin-black: #1c1a1a;
    --bronze: #8a5a2c;
    --bronze-dark: #3a2616;
    --panel-orange: #c84628;
    --panel-line: #6e3018;
    --brand-peach: #f7a766;
    --title-white: #ffffff;
    --tagline-rose: #e4ad9d;
  }
  * { margin: 0; padding: 0; box-sizing: border-box; }
  html, body { width: 1200px; height: 639px; overflow: hidden; }
  body { background: var(--backdrop); position: relative; }

  .label-face {
    position: absolute;
    left: 382px; top: 132px;
    width: 452px; height: 460px;
    background: var(--tin-black);
    overflow: hidden;
  }
  .lattice-pattern {
    position: absolute;
    left: 0; top: 0;
    width: 452px; height: 360px;
    background:
      radial-gradient(circle at 50% 40%, rgba(138,90,44,0.55), rgba(58,38,22,0.35) 70%),
      var(--bronze-dark);
  }
  .label-frame {
    position: absolute;
    left: 98px; top: 122px;
    width: 260px; height: 286px;
    background: var(--tin-black);
    border: 2px solid var(--bronze);
  }
  .flavour-panel {
    position: absolute;
    left: 7px; top: 7px;
    width: 242px; height: 268px;
    background: var(--panel-orange);
    border: 2px solid var(--panel-line);
    text-align: center;
  }
  .brand-name {
    position: absolute; left: 0; right: 0; top: 64px;
    font-family: "Josefin Sans", sans-serif;
    font-weight: 300;
    font-size: 50px;
    line-height: 1;
    letter-spacing: 1px;
    color: var(--brand-peach);
  }
  .tea-name {
    position: absolute; left: 0; right: 0; top: 132px;
    font-family: "Libre Baskerville", serif;
    font-size: 22px;
    line-height: 1;
    letter-spacing: 1.5px;
    color: var(--title-white);
  }
  .tea-tagline {
    position: absolute; left: 0; right: 8px; top: 160px;
    font-family: "Libre Baskerville", serif;
    font-style: italic;
    font-size: 17px;
    line-height: 1;
    letter-spacing: 0.5px;
    color: var(--tagline-rose);
  }
  .pack-contents {
    position: absolute; left: 0; right: 0; top: 228px;
    font-family: "Oswald", sans-serif;
    font-weight: 300;
    font-size: 14px;
    line-height: 1;
    letter-spacing: 1px;
    color: var(--title-white);
  }
</style>
</head>
<body>
  <main class="label-face">
    <div class="lattice-pattern" role="img" aria-label="Geometric bronze line lattice pattern on black"></div>
    <section class="label-frame">
      <div class="flavour-panel">
        <p class="brand-name">VELAN</p>
        <h1 class="tea-name">HIBISCUS TEA</h1>
        <p class="tea-tagline">Bold &amp; Uplifting</p>
        <p class="pack-contents">25 BAGS , 50g</p>
      </div>
    </section>
  </main>
</body>
</html>
```